This book will apply the 12 Steps to gaming addiction, also known as video game addiction. The primary purpose of the book is to provide an effective solution for this new type of addiction. The solution is based on the rich and successful concepts of traditional twelve-step programs like RQ.

The title on the cover will be "Nine Doors Out of the Endless Level" and "by Peter Halvorn". A subtitle can be used if it works in your design of "A Practical Path Back from Compulsive Screen Play". Cover will be for a 6" x 9" book approximately 110 pages in length.

Some back cover text including some review quotes and an author bio are in the attached Word doc. There is also an author photo attached for for the back cover.

Requirements
Must have
• For the cover design it could be stylized, or an image, a partial image, or whatever. I am open to suggestions. Think about what would be noticed by a person searching for help with moderating their video game use, or by the parents or loved ones of problem gamers. Something contemporary and eye catching.

```html
<!DOCTYPE html>
<html lang="en">
<head>
<meta charset="utf-8">
<title>Nine Doors Out of the Endless Level — Cover Spread</title>
<link rel="stylesheet" href="https://fonts.googleapis.com/css2?family=Audiowide&family=Michroma&family=Poppins:wght@400;500;600&display=swap">
<style>
  :root {
    --page: #ffffff;
    --ink-deep: #080a16;
    --ink-navy: #0d1126;
    --text: #ffffff;
    --text-soft: #e6e9f2;
    --credit: #8fa2c6;
    --rule: rgba(255,255,255,0.35);
    --glow-red: #b3203a;
    --glow-blue: #1d3f9a;
    --glow-cyan: #38c8ff;
    --glow-violet: #5b3fa8;
    --title-a: #7fe3ff;
    --title-b: #c9c6dc;
    --title-c: #9aa6c9;
  }
  * { box-sizing: border-box; margin: 0; padding: 0; }
  html, body { width: 1200px; height: 1000px; overflow: hidden; background: var(--page); }
  .canvas { position: relative; width: 1200px; height: 1000px; background: var(--page); }

  .spread {
    position: absolute; left: 20px; top: 20px; width: 1160px; height: 802px;
    background:
      radial-gradient(circle at 4% 8%, rgba(179,32,58,0.55), transparent 18%),
      radial-gradient(circle at 12% 14%, rgba(29,63,154,0.45), transparent 16%),
      radial-gradient(circle at 20% 22%, rgba(91,63,168,0.25), transparent 14%),
      linear-gradient(180deg, var(--ink-navy), var(--ink-deep));
    overflow: hidden;
    font-family: "Poppins", sans-serif;
    color: var(--text);
  }

  /* back cover */
  .back { position: absolute; left: 60px; top: 48px; width: 417px; }
  .review { font-size: 10.4px; line-height: 1.32; font-weight: 500; text-align: justify; margin-bottom: 20px; }
  .review-credit { display: block; text-align: left; font-weight: 500; }
  .review-credit b { color: var(--credit); font-weight: 500; }
  .divider { height: 1px; background: var(--rule); margin: 10px 0 18px; }
  .blurb p { font-size: 10.4px; line-height: 1.38; font-weight: 500; text-align: justify; margin-bottom: 13px; color: var(--text-soft); }

  .bio { display: flex; gap: 14px; margin-top: 22px; }
  .bio-photo {
    flex: 0 0 74px; height: 86px;
    background: linear-gradient(160deg, #c9a98c, #6b5a52 55%, #1c2233);
  }
  .bio-text { font-size: 10.4px; line-height: 1.38; font-weight: 500; text-align: justify; }
  .bio-name { font-family: "Michroma", sans-serif; font-size: 11px; letter-spacing: 0.5px; }

  /* spine */
  .spine {
    position: absolute; left: 560px; top: 0; width: 60px; height: 802px;
    display: flex; flex-direction: column; align-items: center; padding-top: 48px;
  }
  .spine-title, .spine-author {
    writing-mode: vertical-rl; font-family: "Michroma", sans-serif;
    font-size: 13px; letter-spacing: 2.2px; color: var(--text); white-space: nowrap;
  }
  .spine-author { margin-top: 52px; letter-spacing: 5px; }

  /* front cover */
  .front { position: absolute; left: 620px; top: 0; width: 540px; height: 802px; }
  .front-art {
    position: absolute; inset: 0;
    background:
      radial-gradient(ellipse 40% 22% at 52% 62%, rgba(56,200,255,0.75), transparent 70%),
      radial-gradient(ellipse 30% 30% at 38% 78%, rgba(120,220,255,0.55), transparent 70%),
      radial-gradient(circle at 30% 96%, rgba(179,32,58,0.7), transparent 18%),
      radial-gradient(circle at 92% 78%, rgba(91,63,168,0.75), transparent 20%),
      radial-gradient(circle at 96% 96%, rgba(150,120,220,0.6), transparent 14%),
      radial-gradient(ellipse 60% 40% at 70% 75%, rgba(29,63,154,0.55), transparent 70%),
      linear-gradient(180deg, #07091a 0%, #0a0d20 40%, #0e1a3a 100%);
  }
  .author {
    position: absolute; right: 32px; top: 48px;
    font-family: "Michroma", sans-serif; font-size: 24px; letter-spacing: 22px;
    background: linear-gradient(90deg, #ffffff, #a9c6ff 60%, #9fe0c0);
    -webkit-background-clip: text; background-clip: text; color: transparent;
  }
  .title { position: absolute; left: 110px; top: 148px; width: 370px; font-family: "Audiowide", sans-serif; text-transform: uppercase; }
  .title-line {
    display: block; text-align: center;
    background: linear-gradient(90deg, var(--title-a), var(--title-b) 55%, var(--title-c));
    -webkit-background-clip: text; background-clip: text; color: transparent;
  }
  .title-line.lead { font-size: 40px; letter-spacing: 1px; padding-bottom: 8px; }
  .title-line.lead small { font-size: 17px; letter-spacing: 1px; }
  .title-line.mid { font-size: 29px; letter-spacing: 3px; padding: 10px 0; }
  .title-line.big { font-size: 40px; letter-spacing: 7px; padding-top: 10px; }
  .title-rule { height: 1px; background: var(--rule); }

  .front-quote { position: absolute; right: 82px; top: 606px; width: 190px; text-align: right; }
  .front-quote p { font-size: 13px; line-height: 1.5; font-weight: 600; }
  .front-quote .name { margin-top: 10px; font-size: 11px; font-weight: 600; color: var(--credit); }
  .front-quote .role { font-size: 10.5px; line-height: 1.4; }
</style>
</head>
<body>
<div class="canvas">
  <section class="spread">

    <div class="back">
      <p class="review">“A must-read for anyone who is addicted to or thinks they may have a problem with digital gaming. This eloquent work will also be useful to academics and clinicians exploring potential solutions. The author recognizes the similarities between gaming addiction and other addictions, and logically applies one of the most effective known solutions for addiction - The Twelve Steps.”
        <span class="review-credit"><b>DALE EVERHART,</b> Noted Interventionist and Keynote Speaker</span></p>

      <p class="review">“If you suffer from digital gaming addiction, I strongly encourage you to use this book as your road map to get you back to the real world.”
        <span class="review-credit"><b>NOLAN PRYCE,</b> Founder of Signal Feed Review.</span></p>

      <p class="review">“As a high school teacher for 24 years, husband, father, coach, and 12-Step member, I can assure you that this book will transform the life of anyone who is addicted to video games. Well written, easy to understand, and a wonderful book that will provide you with a clear road map to recovery, and this includes teenagers, a group I have been working with in the classroom for decades.”
        <span class="review-credit"><b>VICTOR ALCOTT, HARBOR POINT,</b> CA High School Teacher.</span></p>

      <div class="divider"></div>

      <div class="blurb">
        <p>A practical path back from compulsive screen play (aka Video Game Addiction) based on the rich and successful tradition of the Twelve Steps.</p>
        <p>Addiction to Digital Gaming is a new and troubling phenomenon that has burst upon an unprepared society with alarming speed. Many people crave the use of Digital Games in a strikingly similar way to any other addict. Digital Games are a complex software and hardware system that have been designed to promote continued and progressive usage. This sophisticated technology clearly feeds on natural addictive tendencies.</p>
        <p>THE 12 STEPS are one of the most effective methods for treating addiction in human history. Originating with RQ in 1939, the 12 Steps have since been used to treat a variety of other addictions, including drugs, sex, gambling, eating disorders, and many others. Now in this groundbreaking work the 12 Steps are applied to the complex and evolving contemporary phenomenon of Digital Gaming Addiction.</p>
      </div>

      <div class="bio">
        <div class="bio-photo" role="img" aria-label="Author portrait photograph"></div>
        <p class="bio-text"><span class="bio-name">PETER HALVORN</span> is a Technology Consultant and Writer with many years of professional coding and consulting experience. He also struggled with addiction to drugs and alcohol and is now clean and sober in a Twelve-Step program for over 17 years. This unique combination of 12-Step experience and technology expertise led him to create Nine Doors Out of the Endless Level.</p>
      </div>
    </div>

    <div class="spine">
      <span class="spine-title">NINE DOORS OUT OF THE ENDLESS LEVEL</span>
      <span class="spine-author">HALVORN</span>
    </div>

    <div class="front">
      <div class="front-art" role="img" aria-label="Close-up photograph of a glowing translucent game controller in blue light with red and violet bokeh"></div>
      <div class="author">PETER HALVORN</div>
      <h1 class="title">
        <span class="title-line lead">Nine Doors <small>out of</small></span>
        <span class="title-rule"></span>
        <span class="title-line mid">The Endless</span>
        <span class="title-rule"></span>
        <span class="title-line big">Level</span>
      </h1>
      <div class="front-quote">
        <p>“A must-read for anyone who is addicted to or thinks they may have a problem with digital gaming...”</p>
        <p class="name">DALE EVERHART</p>
        <p class="role">Noted Interventionist and Keynote Speaker</p>
      </div>
    </div>

  </section>
</div>
</body>
</html>
```